Card Design for my dog training business Brightpaw Obedience

Need a business card design for my dog training business with my new logo. Want the card to come off professional yet fun. Want it to be very eye catchy as well. I normally have these at vet clinics, pet stores, and groomers. so need it to look better than my competitors.
Target Market(s)
dog owners
Industry/Entity Type
Dog Training
Contact Information for Business Card
needs logo, my name and info
Font styles to use
Serif
Colors
0255a3
ffffff
ec1f27
000000
333333
fbfbfb
Requirements
Must have
- Brightpaw Obedience
- Felix Orland
- 415 903 2276
- info@brightpawobedience.example
- www.brightpawobedience.example

```html
<!DOCTYPE html>
<html lang="en">
<head>
<meta charset="UTF-8">
<title>Brightpaw Obedience — Business Card</title>
<link rel="stylesheet" href="https://fonts.googleapis.com/css2?family=Noto+Serif:ital,wght@0,400;0,700;1,400&display=swap">
<style>
  :root {
    --brand-blue: #0255a3;
    --brand-red: #ec1f27;
    --ink: #333333;
    --ink-dark: #000000;
    --paper: #fbfbfb;
    --white: #ffffff;
    --backdrop: #c9c9c9;
  }
  * { box-sizing: border-box; margin: 0; padding: 0; }
  html, body {
    width: 1200px;
    height: 576px;
    overflow: hidden;
    background: var(--backdrop);
    font-family: "Noto Serif", Georgia, serif;
    color: var(--ink);
  }
  .stage {
    position: relative;
    width: 1200px;
    height: 576px;
  }
  .card {
    position: absolute;
    top: 138px;
    width: 484px;
    height: 294px;
    background: var(--paper);
    border-radius: 12px;
    overflow: hidden;
    box-shadow: 0 3px 8px rgba(0, 0, 0, 0.25);
  }
  .card--front { left: 82px; }
  .card--back { left: 602px; }

  /* Front */
  .front-brand {
    position: absolute;
    top: 0;
    left: 0;
    width: 100%;
    height: 254px;
    display: flex;
    flex-direction: column;
    align-items: center;
    justify-content: center;
    gap: 12px;
  }
  .brand-mark {
    width: 22px;
    height: 22px;
    border-radius: 50%;
    background: var(--ink);
  }
  .brand-name {
    font-weight: 400;
    font-size: 24px;
    letter-spacing: 0.5px;
    color: var(--ink);
  }
  .tagline-band {
    position: absolute;
    left: 0;
    top: 254px;
    width: 100%;
    height: 30px;
    background: var(--brand-blue);
    display: flex;
    align-items: center;
    justify-content: center;
  }
  .tagline {
    font-style: italic;
    font-size: 11px;
    color: var(--white);
  }

  /* Back */
  .back-brand {
    position: absolute;
    left: 24px;
    top: 96px;
    display: flex;
    align-items: center;
    gap: 8px;
  }
  .back-brand .brand-mark {
    width: 14px;
    height: 14px;
    background: var(--brand-blue);
  }
  .back-brand .brand-name {
    font-size: 16px;
    color: var(--brand-blue);
  }
  .holder {
    position: absolute;
    right: 24px;
    top: 147px;
    text-align: right;
  }
  .holder-name {
    font-size: 19px;
    color: var(--brand-blue);
    line-height: 1.2;
  }
  .holder-title {
    font-size: 12px;
    color: var(--ink);
    margin-top: 2px;
  }
  .divider {
    position: absolute;
    left: 24px;
    right: 24px;
    top: 203px;
    height: 1.5px;
    background: var(--brand-red);
  }
  .contact-list {
    position: absolute;
    left: 24px;
    top: 218px;
    list-style: none;
  }
  .contact-item {
    display: flex;
    align-items: center;
    gap: 10px;
    height: 19px;
    font-size: 12px;
    color: var(--ink);
  }
  .contact-icon {
    width: 11px;
    height: 11px;
    fill: var(--brand-blue);
    flex: none;
  }
</style>
</head>
<body>
<main class="stage">
  <section class="card card--front" aria-label="Card front">
    <div class="front-brand">
      <span class="brand-mark" aria-hidden="true"></span>
      <span class="brand-name">Brightpaw Obedience</span>
    </div>
    <div class="tagline-band">
      <p class="tagline">“Training dogs across Texas one dog at a time.”</p>
    </div>
  </section>

  <section class="card card--back" aria-label="Card back">
    <div class="back-brand">
      <span class="brand-mark" aria-hidden="true"></span>
      <span class="brand-name">Brightpaw Obedience</span>
    </div>
    <div class="holder">
      <p class="holder-name">Felix Orland</p>
      <p class="holder-title">Dog Trainer</p>
    </div>
    <div class="divider"></div>
    <ul class="contact-list">
      <li class="contact-item">
        <svg class="contact-icon" viewBox="0 0 12 12" aria-hidden="true">
          <path d="M1 3.5 Q6 0.5 11 3.5 L10 5 L8 4.5 L8 3.5 Q6 3 4 3.5 L4 4.5 L2 5 Z"/>
          <path d="M3 6 L9 6 L10.5 11 L1.5 11 Z"/>
        </svg>
        <span>415 903 2276</span>
      </li>
      <li class="contact-item">
        <svg class="contact-icon" viewBox="0 0 12 12" aria-hidden="true">
          <path d="M0.5 2 H11.5 V10 H0.5 Z M1.5 3 L6 6.5 L10.5 3 Z" fill-rule="evenodd"/>
        </svg>
        <span>info@brightpawobedience.example</span>
      </li>
      <li class="contact-item">
        <svg class="contact-icon" viewBox="0 0 12 12" aria-hidden="true">
          <circle cx="6" cy="6" r="5.5"/>
          <path d="M0.5 6 H11.5 M6 0.5 V11.5 M6 0.5 Q2.5 6 6 11.5 M6 0.5 Q9.5 6 6 11.5" stroke="#fbfbfb" stroke-width="0.8" fill="none"/>
        </svg>
        <span>www.brightpawobedience.example</span>
      </li>
    </ul>
  </section>
</main>
</body>
</html>
```